Personal training and nutrition business needs business card design

We need a business card that outlays our services and invites potential customers to join our team and take the first step to a healthier and more enjoyable life. We cater for any level of fitness and specialize in weight loss and conditioning, strength training, muscle gain and strength endurance. Whether you are just starting off or need some help getting to the next level of your journey we are here to get the job done.
We specialize in one on one or one on two personal training sessions and each program will be custom made to suit individual fitness goals of our clients

```html
<!DOCTYPE html>
<html lang="en">
<head>
<meta charset="utf-8">
<title>Stride &amp; Pace – Business Card</title>
<link rel="stylesheet" href="https://fonts.googleapis.com/css2?family=Exo+2:ital,wght@0,800;1,800&family=Oswald:wght@500&family=Roboto:wght@400&display=swap">
<style>
  :root {
    --page: #2a2a2a;
    --card: #161616;
    --emboss: #3a3a3a;
    --violet: #a25bb0;
    --violet-deep: #5f3b88;
    --violet-top: #a45a9e;
    --edge: #7a4fb8;
    --ink: #121212;
    --white: #f1f1f1;
    --text: #e6e6e6;
  }
  * { margin: 0; padding: 0; box-sizing: border-box; }
  html, body { width: 1200px; height: 1138px; overflow: hidden; background: var(--page); }
  .card {
    position: absolute;
    width: 620px; height: 374px;
    background: var(--card);
    border-radius: 14px;
    overflow: hidden;
  }
  .card--front { left: 274px; top: 186px; }
  .card--back  { left: 276px; top: 608px; }

  .front-brand {
    position: absolute; left: 0; right: 0; top: 140px;
    text-align: center;
    font: 800 58px/1 "Exo 2", sans-serif;
    color: var(--emboss);
    letter-spacing: 1px;
  }
  .tagline {
    font-family: "Oswald", sans-serif;
    font-weight: 500;
    text-transform: uppercase;
    letter-spacing: 1.2px;
  }
  .front-tagline {
    position: absolute; left: 0; right: 0; top: 334px;
    text-align: center; font-size: 13px; color: var(--violet);
  }

  .back-panel { position: absolute; left: 0; top: 0; width: 310px; height: 374px; }
  .back-brand {
    position: absolute; left: 46px; top: 80px; width: 230px;
    text-align: center;
  }
  .back-brand .dot {
    display: block; width: 62px; height: 62px; margin: 0 auto 18px;
    border-radius: 50%; background: var(--white);
  }
  .back-brand .name {
    font: 800 40px/0.95 "Exo 2", sans-serif; color: var(--ink);
  }
  .back-brand .tagline { margin-top: 10px; font-size: 9px; color: var(--white); }

  .contact { position: absolute; left: 344px; top: 88px; font-family: "Roboto", sans-serif; color: var(--text); }
  .contact .person { font: italic 800 25px/1 "Exo 2", sans-serif; color: var(--violet); letter-spacing: 0.5px; }
  .contact .role { font-size: 16px; margin-top: 6px; }
  .contact ul { list-style: none; margin-top: 28px; }
  .contact li { display: flex; align-items: center; font-size: 16px; height: 24px; }
  .contact li svg { width: 14px; height: 14px; margin-right: 18px; fill: var(--violet); }
  .contact address { font-style: normal; font-size: 16px; line-height: 24px; margin-top: 4px; }
</style>
</head>
<body>
  <section class="card card--front">
    <div class="front-brand">STRIDE &amp; PACE</div>
    <p class="tagline front-tagline">Personal training.&nbsp; Nutrition. Motivation</p>
  </section>

  <section class="card card--back">
    <svg class="back-panel" viewBox="0 0 310 374" aria-hidden="true">
      <defs>
        <linearGradient id="panelFill" x1="0" y1="0" x2="0" y2="1">
          <stop offset="0" stop-color="#a45a9e"/>
          <stop offset="1" stop-color="#5f3b88"/>
        </linearGradient>
      </defs>
      <path d="M0 0 H236 Q326 187 232 374 H0 Z" fill="#7a4fb8"/>
      <path d="M0 0 H232 Q318 187 226 374 H0 Z" fill="#b263a8" opacity="0.8"/>
      <path d="M0 0 H228 Q312 187 222 374 H0 Z" fill="url(#panelFill)"/>
    </svg>
    <div class="back-brand">
      <span class="dot"></span>
      <div class="name">STRIDE<br>&amp; PACE</div>
      <p class="tagline">Personal training.&nbsp; Nutrition. Motivation</p>
    </div>

    <div class="contact">
      <h1 class="person">SAM CARTER</h1>
      <p class="role">Personal Trainer</p>
      <ul>
        <li><svg viewBox="0 0 16 16"><path d="M2 5c0-2 3-3 6-3s6 1 6 3v1h-3V5H5v1H2zM4 7h8l2 7H2z"/></svg>+12 (555) 014-2290</li>
        <li><svg viewBox="0 0 16 16"><path d="M1 3h14v10H1zM2 4l6 5 6-5"/></svg>sam@strideandpace.com</li>
        <li><svg viewBox="0 0 16 16"><circle cx="8" cy="8" r="7"/></svg>www.strideandpace.com</li>
      </ul>
      <address>128 Maple Ridge Drive<br>Lakeview Texas 75000</address>
    </div>
  </section>
</body>
</html>
```